Business Cards for Volmont Hayes, a law firm

We changed our firm's name from "Volmont & Hayes LLP" to "Volmont Hayes", we need to update our cards with a new design. We like the overall look of the back but the front side of the cards (see attached mockup) needs a refreshed look. I also attach our current logo so you can get rid of that LLP and &. We have a new address as well (not same as on mockup).

Target Market(s)

Clients of law firm

Industry/Entity Type

Law Firm

Contact Information for Business Card

Frontsides:

Lorenzo T. Volmont
Partner
Tel: (416) 555-0172 ext. 101
Fax: (647) 555-0139
Email: lvolmont@vhlegal.example

Simon P. Hayes
Partner
Tel: (416) 555-0172 ext. 102
Fax: (647) 555-0139
Email: simonhayes@vhlegal.example

Mark E. Dorsan
Barrister
Tel: (416) 555-0172 ext. 104
Fax: (647) 555-0139
Email: mdorsan@vhlegal.example

The back side should be crimson red (see mockup) with the logo (please update it to remove the & and the LLP, you can modify it a bit to make it tasteful if need be). Our new address is

82 Marlow Rd W, Suite 710
Toronto, ON M5K 0Z9

After our address, please also include our website www.vhlegal.example

Font styles to use
Sans Serif

Colors
ec2027
ffffff
000000

Requirements
Must have
• PLEASE NOTE: our firm's colour is more of a darker/crimson red, not a vibrant red.
• The front should have space for the lawyer's name, title, phone number (with extension), fax number, and email.
• If you're going to add those yourself, the info for the frontside is in the "Business Card Details" section (three lawyers that need their own cards).
Nice to have
• We like the backside of our current cards, just update it with our new address (one address now instead of 2), and a slightly modified logo (not a new logo altogether).
• The frontside should be refreshed with a better look (think minimalist, professional and modern), although still predominantly white-based background.
Should not have
• No scales of justice or other cheesy lawyer stereotype symbols! :-)

```html
<!DOCTYPE html>
<html lang="en">
<head>
<meta charset="utf-8">
<title>Volmont Hayes — Business Card Front</title>
<link href="https://fonts.googleapis.com/css2?family=Barlow:wght@700&family=Montserrat:wght@300;400&family=Roboto:wght@700&display=swap" rel="stylesheet">
<style>
  :root {
    --crimson: #d3262e;
    --ink: #111111;
    --paper: #ffffff;
    --rule: #e8e8e8;
  }
  html, body {
    margin: 0;
    padding: 0;
    width: 1200px;
    height: 622px;
    overflow: hidden;
    background: var(--paper);
  }
  .card {
    position: relative;
    width: 1200px;
    height: 622px;
    background: var(--paper);
  }
  .brand {
    position: absolute;
    left: 0;
    top: 0;
    width: 535px;
    height: 622px;
    display: flex;
    flex-direction: column;
    align-items: center;
    justify-content: center;
    gap: 22px;
  }
  .brand-dot {
    width: 86px;
    height: 86px;
    border-radius: 50%;
    background: var(--crimson);
  }
  .brand-name {
    font-family: "Roboto", Arial, sans-serif;
    font-weight: 700;
    font-size: 38px;
    color: var(--ink);
    letter-spacing: 0.2px;
    margin: 0;
  }
  .divider {
    position: absolute;
    left: 535px;
    top: 103px;
    width: 4px;
    height: 423px;
    background: var(--rule);
  }
  .person {
    position: absolute;
    left: 673px;
    top: 211px;
  }
  .person-name {
    font-family: "Barlow", Arial, sans-serif;
    font-weight: 700;
    font-size: 34px;
    letter-spacing: 1.2px;
    color: var(--ink);
    margin: 0;
    line-height: 1.1;
  }
  .person-title {
    font-family: "Montserrat", Arial, sans-serif;
    font-weight: 300;
    font-size: 26px;
    letter-spacing: 0.6px;
    color: var(--crimson);
    margin: 2px 0 0;
  }
  .contact {
    position: absolute;
    left: 667px;
    top: 358px;
    list-style: none;
    margin: 0;
    padding: 0;
  }
  .contact-item {
    display: flex;
    align-items: center;
    gap: 12px;
    height: 38px;
    font-family: "Montserrat", Arial, sans-serif;
    font-weight: 300;
    font-size: 27px;
    letter-spacing: 0.6px;
    color: var(--ink);
  }
  .contact-icon {
    width: 26px;
    height: 26px;
    fill: var(--crimson);
    flex: none;
  }
</style>
</head>
<body>
  <main class="card">
    <section class="brand">
      <div class="brand-dot"></div>
      <p class="brand-name">Volmont Hayes</p>
    </section>

    <div class="divider"></div>

    <section class="person">
      <h1 class="person-name">Lorenzo T. Volmont</h1>
      <p class="person-title">Partner</p>
    </section>

    <ul class="contact">
      <li class="contact-item">
        <svg class="contact-icon" viewBox="0 0 24 24" aria-hidden="true">
          <path d="M6.6 10.8a15.2 15.2 0 0 0 6.6 6.6l2.2-2.2a1 1 0 0 1 1-.25 11.4 11.4 0 0 0 3.6.6 1 1 0 0 1 1 1V20a1 1 0 0 1-1 1A17 17 0 0 1 3 4a1 1 0 0 1 1-1h3.5a1 1 0 0 1 1 1c0 1.25.2 2.45.6 3.6a1 1 0 0 1-.25 1z"/>
        </svg>
        <span>(416) 555-0172 ext. 101</span>
      </li>
      <li class="contact-item">
        <svg class="contact-icon" viewBox="0 0 24 24" aria-hidden="true">
          <path d="M6 2h10l2 2v4H6z M3 9h18a1 1 0 0 1 1 1v7h-4v5H6v-5H2v-7a1 1 0 0 1 1-1z M8 15v5h8v-5z"/>
        </svg>
        <span>(647) 555-0139</span>
      </li>
      <li class="contact-item">
        <svg class="contact-icon" viewBox="0 0 24 24" aria-hidden="true">
          <path d="M2 5h20v2l-10 6L2 7z M2 9l10 6 10-6v10H2z"/>
        </svg>
        <span>lvolmont@vhlegal.example</span>
      </li>
    </ul>
  </main>
</body>
</html>
```